Road Construction Company needs business cards

We would like a new business card designed for our business.

We're a road construction company based in Qld, Australia.

Can the business card please have the following information on it.

Name: Warren Halbeck
Position: General Manager
Phone: 0472 915 348
Email: Warren.halbeck@tovrin.com.au
Address: 87 Marrow Ave, Pendlebay, QLD, 4023
Website: www.tovrin.com.au

Visually we'd like the card to be professional and simple.

Attached is our logo.

Our website is www.tovrin.com.au

Target Market(s)

Men aged 25-60

Contact Information for Business Card

As listed in project description

Font styles to use
Serif

Requirements
Must have
• Large logo on back of card

```html
<!DOCTYPE html>
<html lang="en">
<head>
<meta charset="utf-8">
<title>Tovrin Business Card</title>
<link rel="stylesheet" href="https://fonts.googleapis.com/css2?family=Montserrat:wght@400;500;700&display=swap">
<style>
  :root {
    --backdrop: #dcdcdc;
    --brand-navy: #0b4595;
    --brand-blue: #1158a9;
    --brand-sky: #2487c2;
    --card-white: #f3f3f3;
    --text-grey: #555a60;
    --name-blue: #0c4a9c;
  }
  * { margin: 0; padding: 0; box-sizing: border-box; }
  html, body {
    width: 1200px; height: 1200px; overflow: hidden;
    background: var(--backdrop);
    font-family: "Montserrat", Arial, sans-serif;
  }
  .canvas { position: relative; width: 1200px; height: 1200px; }
  .card {
    position: absolute; left: 234px; width: 731px; height: 418px;
    overflow: hidden;
  }
  .card-front { top: 160px; }
  .card-back { top: 632px; background: linear-gradient(120deg, #e4e4e4 0%, var(--card-white) 60%, #f7f7f7 100%); }

  .front-pattern {
    position: absolute; inset: 0;
    background: linear-gradient(115deg, #0b4a9a 0%, var(--brand-blue) 55%, #1566b0 100%);
  }
  .front-brand {
    position: absolute; left: 330px; top: 258px; width: 290px;
    text-align: center; color: #f4f4f4;
    font-weight: 700; font-size: 50px; letter-spacing: 2px; line-height: 1;
  }

  .back-brand {
    position: absolute; left: 0; right: 0; top: 78px;
    text-align: center; color: var(--brand-navy);
    font-weight: 700; font-size: 50px; letter-spacing: 2px; line-height: 1;
  }
  .contact {
    position: absolute; left: 61px; top: 196px;
    color: var(--text-grey); font-size: 19px; line-height: 28px;
  }
  .address { margin-bottom: 6px; }
  .contact-row { display: flex; align-items: center; gap: 9px; }
  .contact-row svg { width: 17px; height: 17px; flex: none; }
  .person {
    position: absolute; right: 62px; top: 262px; text-align: right;
  }
  .person-name { color: var(--name-blue); font-weight: 700; font-size: 30px; line-height: 1.1; }
  .person-role { color: var(--text-grey); font-size: 19px; margin-top: 6px; }
  .footer-bands { position: absolute; left: 0; bottom: 0; width: 731px; height: 60px; }
</style>
</head>
<body>
<div class="canvas">
  <section class="card card-front">
    <div class="front-pattern" role="img" aria-label="Blue background with a grid of embossed upward arrow shapes"></div>
    <div class="front-brand">TOVRIN</div>
  </section>

  <section class="card card-back">
    <div class="back-brand">TOVRIN</div>

    <div class="contact">
      <p class="address">87 Marrow Ave, Pendlebay,<br>QLD, 4023</p>
      <p class="contact-row">
        <svg viewBox="0 0 24 24" aria-hidden="true"><path fill="#0b4595" d="M6.6 10.8a15 15 0 0 0 6.6 6.6l2.2-2.2c.3-.3.7-.4 1-.2 1.1.4 2.3.6 3.6.6.6 0 1 .4 1 1V20c0 .6-.4 1-1 1A17 17 0 0 1 3 4c0-.6.4-1 1-1h3.5c.6 0 1 .4 1 1 0 1.3.2 2.5.6 3.6.1.3 0 .7-.2 1z"/></svg>
        0472 915 348
      </p>
      <p class="contact-row">
        <svg viewBox="0 0 24 24" aria-hidden="true"><path fill="#0b4595" d="M2 5h20v14H2z"/><path fill="none" stroke="#f3f3f3" stroke-width="1.8" d="M2.5 5.5 12 13l9.5-7.5"/></svg>
        Warren.halbeck@tovrin.com.au
      </p>
      <p class="contact-row">
        <svg viewBox="0 0 24 24" aria-hidden="true"><circle cx="12" cy="12" r="10" fill="#0b4595"/><path fill="none" stroke="#f3f3f3" stroke-width="1.5" d="M2 12h20M12 2c-3.5 3.5-3.5 16.5 0 20M12 2c3.5 3.5 3.5 16.5 0 20"/></svg>
        www.tovrin.com.au
      </p>
    </div>

    <div class="person">
      <p class="person-name">Warren Halbeck</p>
      <p class="person-role">General Manager</p>
    </div>

    <svg class="footer-bands" viewBox="0 0 731 60" aria-hidden="true">
      <rect x="0" y="21" width="480" height="15" fill="var(--brand-sky)"/>
      <path fill="var(--brand-navy)" d="M0 36 H430 C455 36 462 26 472 16 C482 6 490 2 510 2 H731 V60 H0 Z"/>
    </svg>
  </section>
</div>
</body>
</html>
```